Human Resource Consulting practice needs a business card design

We need a business card design (double sided colour) for our Human Resource (HR) consulting practice in regional New South Wales, australia. Our business name is Staff Compass. We support small and medium business across the Mid North Coast of New South Wales by providing them with outsourced HR support, services and products to help them achieve compliance with workplace legislation and across all areas of the employment lifecycle from recruitment to termination and everything in between. Our corporate colours are hot pink and black. The final design should communicate professionalism, trust, people focus.
I have attached the current (old) business card for your reference.

Target Market(s)

Business owners and high level managers

Industry/Entity Type

Business

Contact Information for Business Card

Name
Title
Phone no
Mobile no
Address
PO Box
email address
website

Colors
e34197

Requirements
Must have
• Tempate for changing business card personal details including Name, position title, mobile number, email address.
• Keep current logo and colours as per attached
• Logo must be presented in 2 colours or black only not white
Nice to have
• One side logo and graphic only other side logo and personal details
Should not have
• Should not be the same as the current version (attached) but a modern interpretation.
• Does not need a busy reverse side with our list of services as per current version. I feel this is too busy.
• No photos

```html
<!DOCTYPE html>
<html lang="en">
<head>
<meta charset="utf-8">
<title>Staff Compass – Business Card</title>
<link href="https://fonts.googleapis.com/css2?family=Arimo:wght@400;700&family=Orbitron:wght@500&display=swap" rel="stylesheet">
<style>
  :root {
    --pink: #e3198f;
    --ink: #1f1f21;
    --ink-soft: #3c3c3f;
    --paper: #f7f7f7;
    --grey: #5a5a5e;
    --stage: #e9e7e4;
    --white: #ffffff;
  }
  * { box-sizing: border-box; margin: 0; padding: 0; }
  html, body { width: 1200px; height: 902px; overflow: hidden; }
  body {
    background: var(--stage);
    font-family: "Arimo", Arial, sans-serif;
    position: relative;
  }
  .card {
    position: absolute;
    width: 620px;
    height: 378px;
    border-radius: 4px;
    box-shadow: 0 10px 28px rgba(0,0,0,.25);
    overflow: hidden;
  }
  .logo {
    display: flex;
    align-items: center;
    gap: 10px;
    font-family: "Arimo", Arial, sans-serif;
    font-weight: 700;
    color: var(--pink);
    line-height: 1;
    white-space: nowrap;
  }
  .logo-mark {
    width: 12px; height: 12px;
    background: var(--pink);
    border-radius: 50%;
  }

  /* Front: logo and tagline only */
  .card-front {
    left: 80px; top: 50px;
    background: linear-gradient(135deg, var(--ink-soft) 0%, #2a2a2d 45%, var(--ink) 100%);
  }
  .card-front .logo {
    position: absolute; left: 56px; top: 130px;
    font-size: 46px; letter-spacing: -0.5px;
  }
  .front-rule {
    position: absolute; left: 56px; top: 200px;
    width: 80px; height: 3px; background: var(--pink);
  }
  .tagline {
    position: absolute; left: 56px; top: 222px;
    color: var(--white);
    font-size: 17px;
    letter-spacing: .2px;
  }

  /* Back: contact side */
  .card-back {
    left: 500px; top: 474px;
    background: var(--paper);
  }
  .card-back .logo {
    position: absolute; left: 40px; top: 138px;
    font-size: 32px; letter-spacing: -0.4px;
  }
  .rule {
    position: absolute; left: 40px; right: 40px; top: 178px;
    height: 2px; background: var(--ink);
  }
  .person-name {
    position: absolute; right: 40px; top: 118px;
    font-family: "Orbitron", "Arimo", sans-serif;
    font-weight: 500;
    font-size: 26px;
    color: var(--pink);
    white-space: nowrap;
  }
  .person-title {
    position: absolute; right: 40px; top: 188px;
    font-size: 10.5px;
    letter-spacing: .6px;
    color: var(--grey);
  }
  .address {
    position: absolute; right: 40px; top: 236px;
    text-align: right;
    font-size: 13px;
    line-height: 1.4;
    color: var(--ink);
  }
  .contact-list {
    position: absolute; left: 40px; top: 232px;
    list-style: none;
    font-size: 14px;
    color: var(--ink);
  }
  .contact-list li {
    display: flex; align-items: center; gap: 10px;
    height: 22px;
  }
  .contact-icon {
    width: 16px; height: 16px;
    background: var(--ink-soft);
    border-radius: 2px;
    display: flex; align-items: center; justify-content: center;
  }
  .contact-icon svg { width: 12px; height: 12px; fill: none; stroke: var(--pink); stroke-width: 1.6; }
</style>
</head>
<body>

<section class="card card-front" aria-label="Business card front">
  <div class="logo"><span class="logo-mark"></span>Staff Compass</div>
  <div class="front-rule"></div>
  <p class="tagline">Building Exciting, Engaging &amp; Productive Workplaces</p>
</section>

<section class="card card-back" aria-label="Business card back">
  <p class="person-name">Marlee Hutton</p>
  <div class="logo"><span class="logo-mark"></span>Staff Compass</div>
  <div class="rule"></div>
  <p class="person-title">PRINCIPAL CONSULTANT</p>
  <p class="address">PO Box 218, Riverbend,<br>NSW 2999</p>
  <ul class="contact-list">
    <li><span class="contact-icon"><svg viewBox="0 0 12 12"><path d="M3 1.5h2l.5 2.5-1.2.8a6 6 0 0 0 3 3l.8-1.2 2.4.5v2A1 1 0 0 1 9.5 10 8.5 8.5 0 0 1 2 2.5 1 1 0 0 1 3 1.5z"/></svg></span>02 5550 1234</li>
    <li><span class="contact-icon"><svg viewBox="0 0 12 12"><rect x="3.5" y="1" width="5" height="10" rx="1"/><path d="M5.5 9.2h1"/></svg></span>0400 555 018</li>
    <li><span class="contact-icon"><svg viewBox="0 0 12 12"><rect x="1.5" y="4.5" width="9" height="5" rx=".5"/><path d="M3.5 4.5V1.5h5v3M3.5 9.5v1h5v-1"/></svg></span>02 5550 1260</li>
    <li><span class="contact-icon"><svg viewBox="0 0 12 12"><circle cx="6" cy="6" r="4.5"/><path d="M1.5 6h9M6 1.5c2 2.4 2 6.6 0 9M6 1.5c-2 2.4-2 6.6 0 9"/></svg></span>www.staffcompass.com.au</li>
    <li><span class="contact-icon"><svg viewBox="0 0 12 12"><rect x="1.5" y="3" width="9" height="6"/><path d="M1.5 3L6 6.5 10.5 3"/></svg></span>marlee@staffcompass.com.au</li>
  </ul>
</section>

</body>
</html>
```